Looking for a cool, modern Cannabis Jar Label

I want you to come up with a better, modern look for a label.

I need it sized to 4” x 3” - I plan to print directly to label printer.

I want you to use Photoshop and deliver me a layered PSD file that I can edit and modify the information as needed..

The label information will need to include places for:
(1) Strain Name - most important part of label - larger font size than rest - example Kestrel Mist, PLV #7, Juniper Hollow
(2) Pricing - for Gram, 1/8, 1/4, 1/2. and Ounce
(3) Strain Designation (Hybrid, Indica or Sativa) - maybe color coded, different color for Indica v. Sativa, just an idea
(4) THC and CBD percentages - for example 23% THC and 0.05% CBD
(5) Farm name - a place where we can add the name/logo of the business that produced the product. example - Ovenrow Farms

I have attached a simple mockup showing the information.

I have also attached a few samples of labels we like to give you an idea of the look and feel we are going for.

I am wanting a very clean, modern, classy, readable look.The font will use is Gotham Font.

HI Everyone! Thank you for all of your designs. I am requesting an extension because I need more time to give adequate feedback to the designers. Thank you for your participation and all of your efforts! I will be making a decision soon!

• Gotham Font

• Thank you for your designs. I am sorry i have been slow in providing feedback, things have been really busy around here!
• I wanted to give some group general feedback. After reviewing all of the designs, there is a common theme among all of the designs that I would like to see changed.
• I would like to see the per gram pricing more prominent on the label. This is what most people are looking for when they are purchasing the product. So I would like to see this stand out from the other pricing tiers. As I think about it, they don't all need to be grouped together in a line. You could have the Per Gram pricing front and center some where and then the other pricing tiers grouped together somewhere else on the label.
• This is the order of importance of items on the label. Items at the the top of the list should be bigger than those below it.
• 1. Strain name
• 2. Pricing - being per gram the most important of all prices
• 3. THC/CBD percentages
• 4. Strain Type (indica, sativa, hybrid)
• 5. Farm name/logo
• When laying out these labels, they will be going on rounded jars and they will be on display. Think of jars with fancy labels in a candy store. They need to be eye catchy, appealing, but easy read.
• Thank you for all of your hard work, everyone is doing a great job.
• Best,
• Neta

```html
<!DOCTYPE html>
<html lang="en">
<head>
<meta charset="utf-8">
<title>Alder Ridge Frost – Jar Label</title>
<link rel="stylesheet" href="https://fonts.googleapis.com/css2?family=Montserrat:wght@300;400;500&display=swap">
<style>
  :root {
    --leaf-green: #52893f;
    --sage: #7fa46a;
    --sage-mid: #86ab73;
    --sage-soft: #a3bd92;
    --lime-soft: #b2d69a;
    --mint-pale: #e4efda;
    --ink: #111;
    --paper: #fff;
    --label-font: "Montserrat", "Helvetica Neue", Arial, sans-serif;
  }
  html, body {
    margin: 0;
    padding: 0;
    width: 1200px;
    height: 917px;
    overflow: hidden;
    background: var(--paper);
    font-family: var(--label-font);
  }
  .label {
    position: absolute;
    left: 33px;
    top: 33px;
    width: 1132px;
    height: 849px;
    box-sizing: border-box;
    border: 13px solid var(--leaf-green);
    background: var(--paper);
    overflow: hidden;
  }
  .leaf-art {
    position: absolute;
    left: 0;
    top: 170px;
    width: 760px;
    height: 670px;
    background: radial-gradient(ellipse at 45% 65%, rgba(122,181,80,0.55) 0%, rgba(122,181,80,0.25) 45%, rgba(122,181,80,0) 72%);
  }
  .strain-name {
    position: absolute;
    left: 0;
    right: 0;
    top: 28px;
    margin: 0;
    text-align: center;
    font-weight: 500;
    font-size: 104px;
    line-height: 142px;
    color: var(--leaf-green);
    text-shadow: 2px 3px 4px rgba(0,0,0,0.35);
    letter-spacing: 1px;
  }
  .price-row {
    position: absolute;
    left: 0;
    top: 334px;
    width: 1107px;
    height: 120px;
    display: flex;
  }
  .price {
    position: relative;
    height: 100%;
    display: flex;
    align-items: flex-end;
    justify-content: center;
    padding-bottom: 14px;
    box-sizing: border-box;
    font-weight: 300;
    font-size: 58px;
    color: var(--ink);
  }
  .price .unit {
    position: absolute;
    right: 10px;
    top: 4px;
    font-size: 28px;
    font-weight: 300;
  }
  .price--gram { width: 213px; background: rgba(178,214,154,0.85); }
  .price--eighth { width: 228px; background: rgba(163,189,146,0.9); }
  .price--quarter { width: 226px; background: rgba(134,171,115,0.9); }
  .price--half { width: 227px; background: rgba(163,189,146,0.95); }
  .price--ounce { width: 213px; background: var(--mint-pale); }
  .strain-type {
    position: absolute;
    left: 0;
    top: 471px;
    width: 1107px;
    height: 120px;
    background: var(--leaf-green);
    color: var(--paper);
    text-align: center;
    font-weight: 300;
    font-size: 96px;
    line-height: 120px;
  }
  .potency {
    position: absolute;
    left: 0;
    height: 90px;
    background: rgba(127,164,106,0.92);
    display: flex;
    align-items: center;
  }
  .potency--thc { top: 608px; width: 463px; }
  .potency--cbd { top: 716px; width: 279px; }
  .potency .name {
    flex: 1;
    text-align: center;
    font-size: 44px;
    font-weight: 400;
    color: var(--ink);
  }
  .potency--thc .name { padding-right: 110px; text-align: center; }
  .potency--cbd .name { padding-right: 60px; }
  .potency .value {
    position: absolute;
    right: 0;
    width: 90px;
    height: 90px;
    border-radius: 50%;
    background: var(--mint-pale);
    display: flex;
    align-items: center;
    justify-content: center;
    font-size: 40px;
    color: var(--ink);
  }
  .potency .value sup { font-size: 18px; margin-top: -14px; }
  .grower {
    position: absolute;
    left: 754px;
    top: 591px;
    width: 353px;
    height: 233px;
    background: var(--leaf-green);
  }
  .grower .heading {
    position: absolute;
    left: 6px;
    right: 0;
    top: 0;
    height: 56px;
    background: var(--sage);
    text-align: center;
    font-size: 40px;
    line-height: 56px;
    color: var(--ink);
    letter-spacing: 2px;
  }
  .grower .farm {
    position: absolute;
    left: 6px;
    right: 0;
    top: 58px;
    bottom: 0;
    background: var(--paper);
    display: flex;
    align-items: center;
    justify-content: center;
    gap: 14px;
  }
  .grower .mark { width: 70px; height: 70px; flex: none; }
  .grower .farm-name {
    font-size: 34px;
    font-weight: 500;
    color: var(--ink);
    line-height: 1.1;
  }
</style>
</head>
<body>
  <main class="label">
    <div class="leaf-art" role="img" aria-label="Soft green cannabis leaf illustration behind the label content"></div>

    <h1 class="strain-name">Alder Ridge<br>Frost</h1>

    <section class="price-row" aria-label="Pricing">
      <div class="price price--gram"><span class="unit">g.</span>$10</div>
      <div class="price price--eighth"><span class="unit">1/8</span>$35</div>
      <div class="price price--quarter"><span class="unit">1/4</span>$70</div>
      <div class="price price--half"><span class="unit">1/2</span>$140</div>
      <div class="price price--ounce"><span class="unit">Oz</span>$280</div>
    </section>

    <div class="strain-type">Indica</div>

    <div class="potency potency--thc">
      <span class="name">THC</span>
      <span class="value">28<sup>%</sup></span>
    </div>
    <div class="potency potency--cbd">
      <span class="name">CBD</span>
      <span class="value">2<sup>%</sup></span>
    </div>

    <section class="grower">
      <div class="heading">Grown by</div>
      <div class="farm">
        <svg class="mark" viewBox="0 0 70 70" aria-hidden="true">
          <circle cx="35" cy="35" r="32" fill="none" stroke="#111" stroke-width="3"/>
        </svg>
        <span class="farm-name">Ovenrow<br>Farms</span>
      </div>
    </section>
  </main>
</body>
</html>
```